New Business Card Design Project

Use the flyer uploaded and website www.brightoakbuilders.com for inspiration.
List Our Services on Backside of business cards
Marcus Delling
Harborline Builders Inc.
Licensed General Contractors
858-471-6093

Contact Information for Business Card

Use the flyer uploaded and website www.brightoakbuilders.com for inspiration. List Our Services on Backside of business cards Marcus Delling Harborline Builders Inc. Licensed General Contractors 858-471-6093

```html
<!DOCTYPE html>
<html lang="en">
<head>
<meta charset="utf-8">
<title>Harborline Builders – Business Cards</title>
<link href="https://fonts.googleapis.com/css2?family=Cinzel:wght@400;700&family=Montserrat:wght@400;500&display=swap" rel="stylesheet">
<style>
  :root {
    --page-bg: #2a2a2c;
    --card-bg: #141416;
    --ink: #f4f4f4;
    --rule: #bdbdbd;
  }
  * { box-sizing: border-box; margin: 0; padding: 0; }
  html, body { width: 1200px; height: 912px; overflow: hidden; }
  body {
    background: var(--page-bg);
    position: relative;
    font-family: "Montserrat", sans-serif;
    color: var(--ink);
  }
  .card {
    position: absolute;
    width: 560px;
    height: 320px;
    background: var(--card-bg);
    border-radius: 14px;
    box-shadow: 0 18px 40px rgba(0,0,0,0.55);
    overflow: hidden;
  }
  .card--services { left: 60px; top: 110px; }
  .card--contact { left: 580px; top: 480px; }

  .wordmark {
    display: flex;
    align-items: center;
    gap: 10px;
    font-family: "Cinzel", serif;
    font-weight: 400;
    color: var(--ink);
    letter-spacing: 0.04em;
    white-space: nowrap;
  }
  .wordmark__dot {
    width: 10px; height: 10px;
    border: 1.5px solid var(--ink);
    border-radius: 50%;
    flex: none;
  }

  .card--services .wordmark {
    position: absolute;
    top: 104px; left: 0; right: 0;
    justify-content: center;
    font-size: 30px;
  }
  .services {
    position: absolute;
    top: 196px; left: 0; right: 0;
    text-align: center;
    font-size: 17px;
    line-height: 1.55;
    letter-spacing: 0.01em;
  }

  .card--contact .wordmark {
    position: absolute;
    left: 0; width: 300px; top: 178px;
    justify-content: center;
    font-size: 18px;
    gap: 8px;
  }
  .card--contact .wordmark__dot { width: 8px; height: 8px; }
  .divider {
    position: absolute;
    left: 300px; top: 70px;
    width: 1px; height: 190px;
    background: var(--rule);
  }
  .contact {
    position: absolute;
    left: 322px; top: 72px;
  }
  .contact__name {
    font-family: "Cinzel", serif;
    font-weight: 700;
    font-size: 19px;
    letter-spacing: 0.03em;
  }
  .contact__role { font-size: 12.5px; margin-top: 2px; }
  .contact__list { list-style: none; margin-top: 16px; }
  .contact__list li {
    display: flex; align-items: center; gap: 8px;
    font-size: 12.5px; line-height: 1.9;
  }
  .contact__list svg { width: 12px; height: 12px; flex: none; }
  .contact__company { font-size: 12.5px; margin-top: 14px; }
</style>
</head>
<body>

  <section class="card card--services">
    <div class="wordmark"><span class="wordmark__dot"></span>Harborline Builders</div>
    <p class="services">
      Painting • Flooring • Kitchens • Custom Renovations<br>
      Bathrooms • Energy Efficienct Upgrades
    </p>
  </section>

  <section class="card card--contact">
    <div class="wordmark"><span class="wordmark__dot"></span>Harborline Builders</div>
    <div class="divider"></div>
    <div class="contact">
      <h1 class="contact__name">MARCUS DELLING</h1>
      <p class="contact__role">Licensed General Contractors</p>
      <ul class="contact__list">
        <li>
          <svg viewBox="0 0 24 24" aria-hidden="true"><path fill="#f4f4f4" d="M6.6 10.8a15.1 15.1 0 0 0 6.6 6.6l2.2-2.2a1 1 0 0 1 1-.25 11.4 11.4 0 0 0 3.6.57 1 1 0 0 1 1 1V20a1 1 0 0 1-1 1A17 17 0 0 1 3 4a1 1 0 0 1 1-1h3.5a1 1 0 0 1 1 1c0 1.25.2 2.45.57 3.57a1 1 0 0 1-.25 1z"/></svg>
          858-471-6093
        </li>
        <li>
          <svg viewBox="0 0 24 24" aria-hidden="true"><rect x="2" y="5" width="20" height="14" rx="1" fill="#f4f4f4"/><path d="M2.5 5.5 12 13l9.5-7.5" fill="none" stroke="#141416" stroke-width="1.8"/></svg>
          info@brightoakbuilders.com
        </li>
        <li>
          <svg viewBox="0 0 24 24" aria-hidden="true"><circle cx="12" cy="12" r="9.5" fill="none" stroke="#f4f4f4" stroke-width="2"/><path d="M2.5 12h19M12 2.5c3 3 3 16 0 19M12 2.5c-3 3-3 16 0 19" fill="none" stroke="#f4f4f4" stroke-width="1.6"/></svg>
          www.brightoakbuilders.com
        </li>
      </ul>
      <p class="contact__company">Harborline Builders Inc.</p>
    </div>
  </section>

</body>
</html>
```